Vellmore Family Law, legal technician needs a website and design

I need a website for a family law practice. I specialize in collaborative law, unbundled services, and mediation. The website must contain my company logo (file attached), and the website must be a mixture of my personality and my profession. I have attached additional information to explain my personality and profession.

Target Market(s)

Lower through middle-class (income level up to $200,000 per year)

Coding

Coded - Design and coding required

Number of Pages Required

1 page

Requirements
Must have
• Must have enough pages to cover required content. I submitted below some content about the collaborative law process. All of the content is not necessary. However, the website must have enough content to clearly describe the services I offer. Use your professionalism and judgment regarding font, font size, etc.

```html
<!DOCTYPE html>
<html lang="en">
<head>
<meta charset="utf-8">
<title>Vellmore Family Law</title>
<link rel="stylesheet" href="https://fonts.googleapis.com/css2?family=Cinzel:wght@400;600;700&family=Roboto:ital,wght@0,400;0,500;0,700;1,400;1,700&display=swap">
<style>
:root{
  --navy:#0b0d36;
  --navy-2:#141850;
  --gold:#a9a22c;
  --gold-light:#c9c24a;
  --gold-dark:#7d7620;
  --ink:#1e1e1e;
  --muted:#666;
  --light:#f2f2f2;
  --white:#fff;
}
*{margin:0;padding:0;box-sizing:border-box}
html,body{width:1200px;height:5190px;overflow:hidden}
body{font-family:"Roboto",Arial,sans-serif;color:var(--ink);background:var(--white);position:relative}
.abs{position:absolute}
section,header,footer{position:absolute;left:0;width:1200px}
.btn{position:absolute;display:flex;align-items:center;justify-content:center;border-radius:30px;background:linear-gradient(180deg,var(--gold-light),var(--gold-dark));color:#fff;font-family:"Cinzel",Georgia,serif;font-size:17px;letter-spacing:1px;white-space:nowrap}
.eyebrow{font-weight:700;font-size:15px;letter-spacing:.5px;color:var(--ink)}
.h2{font-family:"Cinzel",Georgia,serif;font-weight:600;color:var(--gold);font-size:40px;letter-spacing:1px;white-space:nowrap}
.rule{position:absolute;height:4px;width:100px;background:var(--gold)}
.learn{font-size:12px;font-weight:700;color:var(--gold);letter-spacing:.5px}

/* top bar */
.topbar{top:0;height:40px;background:var(--navy);color:#fff}
.topbar .mail{left:84px;top:13px;font-family:"Cinzel",serif;font-size:11px;font-weight:700}
.topbar .call{left:678px;top:14px;font-family:"Cinzel",serif;font-size:11px}
.topbar .tel{left:925px;top:5px;font-family:"Cinzel",serif;font-size:24px;color:var(--gold-light);white-space:nowrap}

/* nav */
.nav{top:40px;height:91px;background:#fff;border-bottom:1px solid #e6e6e6}
.brand{left:84px;top:16px;display:flex;align-items:center;gap:12px}
.brand .mark{width:50px;height:58px;border:3px solid var(--gold)}
.brand .name{font-family:"Cinzel",serif;color:var(--gold);font-size:21px;line-height:21px;font-weight:600}
.brand .name small{display:block;font-size:9px;line-height:14px;letter-spacing:1px}
.menu{left:334px;top:45px;display:flex;gap:33px;font-size:11px;font-weight:700;color:var(--ink);white-space:nowrap}

/* hero */
.hero{top:131px;height:584px;background:linear-gradient(180deg,#d7a77a 0%,#9a8a86 30%,#4c5068 65%,var(--navy) 100%)}
.hero h1{position:absolute;left:0;width:1200px;top:145px;text-align:center;font-family:"Cinzel",serif;font-weight:400;font-size:62px;color:#fff;letter-spacing:1px}
.hero p{position:absolute;left:205px;width:790px;top:240px;text-align:center;color:#fff;font-size:15px;line-height:29px}

/* about */
.about{top:715px;height:468px;background:var(--navy);color:#fff}
.about .emblem{left:195px;top:20px;width:355px;height:355px;display:flex;align-items:center;justify-content:center}
.about .emblem span{font-family:"Cinzel",serif;font-size:34px;color:var(--gold);font-weight:600;text-align:center;line-height:42px}
.about .label{left:600px;top:18px;font-weight:700;font-size:15px}
.about h2{position:absolute;left:600px;top:42px}
.about .rule{left:600px;top:103px}
.about p{position:absolute;left:600px;top:125px;width:490px;font-size:12.5px;line-height:30px}

/* services */
.services{top:1183px;height:600px;background:#fff}
.services .label{left:86px;top:97px}
.services h2{position:absolute;left:90px;top:123px}
.services .rule{left:90px;top:180px}
.services .vline{left:475px;top:82px;width:2px;height:120px;background:#ccc}
.services .intro{left:560px;top:92px;width:530px;font-size:12.5px;line-height:30px;color:#444}
.svc{position:absolute;top:245px;width:330px}
.svc .icon{width:84px;height:84px}
.svc h3{font-family:"Cinzel",serif;font-weight:600;font-size:18px;margin-top:28px;letter-spacing:.5px}
.svc p{font-size:12.5px;line-height:30px;color:#444;margin-top:8px;width:300px}
.svc .learn{display:block;margin-top:4px}
.svc-div{position:absolute;top:242px;width:1px;height:270px;background:#ccc}

/* video */
.video{top:1783px;height:393px;background:linear-gradient(90deg,#4a4240,#6b6865 45%,#5a5753 70%,#3a3432)}
.play{left:550px;top:147px;width:100px;height:100px;border-radius:50%;background:rgba(169,162,44,.35);display:flex;align-items:center;justify-content:center}
.play i{width:60px;height:60px;border-radius:50%;background:var(--gold);display:flex;align-items:center;justify-content:center}

/* team */
.team{top:2176px;height:605px;background:var(--light)}
.center{position:absolute;left:0;width:1200px;text-align:center}
.card{position:absolute;top:197px;width:237px;height:320px;background:#fff;box-shadow:0 2px 8px rgba(0,0,0,.08);text-align:center}
.card .photo{height:242px;background:linear-gradient(180deg,#d9d9d9,#9c9c9c)}
.card h4{font-family:"Cinzel",serif;font-weight:600;font-size:16px;margin-top:14px;letter-spacing:1px}
.card .learn{display:block;margin-top:6px}
.arrow{position:absolute;width:40px;height:40px;border-radius:50%;background:#fff;box-shadow:0 1px 4px rgba(0,0,0,.15);display:flex;align-items:center;justify-content:center;z-index:2}

/* testimonials */
.testi{top:2781px;height:534px;background:#fff}
.testi .label{left:120px;top:100px}
.testi h2{position:absolute;left:120px;top:123px;font-size:44px}
.testi .rule{left:120px;top:185px}
.testi .qm{left:118px;top:215px;font-size:48px;font-family:Georgia,serif;font-style:italic;color:#999;font-weight:700}
.testi blockquote{position:absolute;left:120px;top:228px;width:870px;font-style:italic;font-size:21px;line-height:38px;color:#333;text-indent:38px}
.testi .avatar{left:120px;top:382px;width:60px;height:60px;border-radius:50%;background:linear-gradient(180deg,#cfcfcf,#7a7a7a)}
.testi .who{left:197px;top:393px;font-style:italic;font-weight:700;font-size:19px;color:var(--gold)}
.testi .role{left:197px;top:420px;font-style:italic;font-weight:700;font-size:11px}
.dot{position:absolute;left:1069px;width:11px;height:11px;border-radius:50%;border:1px solid #aaa}
.dot.on{background:var(--gold);border-color:var(--gold)}

/* blogs */
.blogs{top:3315px;height:745px;background:var(--light)}
.post{position:absolute;top:202px;width:310px;height:422px;background:#fff;box-shadow:0 2px 10px rgba(0,0,0,.1);padding:10px}
.post .thumb{height:200px;border:1px solid #ddd}
.post h4{font-family:"Cinzel",serif;font-weight:400;font-size:17.5px;line-height:27px;margin:22px 0 0 8px}
.post p{font-size:12px;line-height:23px;color:#777;margin:8px 8px 0}
.post .meta{position:absolute;left:18px;right:18px;bottom:18px;border-top:2px solid #333;padding-top:14px;display:flex;justify-content:space-between;font-size:12px}
.post .meta b{font-weight:500;color:var(--gold)}
.blogs .arrow{background:#ddd;width:46px;height:46px}

/* contact */
.contact{top:4060px;height:766px;background:linear-gradient(180deg,var(--navy) 0%,#1a2150 40%,#2a3050 70%,var(--navy) 100%);color:#fff}
.contact h2{font-weight:400}
.info{position:absolute;top:178px;display:flex;gap:14px}
.info b{display:block;color:var(--gold-light);font-weight:500;font-size:16px}
.info span{font-size:13px;line-height:22px}
.form{left:105px;top:268px;width:985px;height:462px;background:#fff;border-radius:20px;border-left:6px solid var(--gold);border-bottom:6px solid var(--gold);color:var(--ink)}
.form .title{left:92px;top:165px;font-family:"Cinzel",serif;font-size:36px;line-height:44px;color:var(--gold)}
.field{position:absolute;width:268px;border-bottom:1px solid #888;font-size:11px;color:#444;height:32px}
.submit{left:298px;top:334px;width:590px;height:44px;border-radius:0;font-size:14px;font-weight:700}

/* footer */
.foot{top:4826px;height:364px;background:var(--navy);color:#fff}
.foot .logo{left:97px;top:42px;display:flex;gap:14px;align-items:center}
.foot .logo i{width:30px;height:30px;border:3px solid var(--gold)}
.foot .logo span{font-family:"Cinzel",serif;font-size:26px;line-height:28px;color:#fff}
.foot .logo small{display:block;font-size:10px;line-height:14px;letter-spacing:1px}
.foot .about-txt{left:97px;top:142px;width:270px;font-size:13.5px;line-height:30px}
.social{left:97px;top:262px;display:flex;gap:10px}
.social i{width:14px;height:14px;border-radius:50%;background:var(--gold)}
.col{position:absolute;top:34px}
.col h5{font-family:"Cinzel",serif;font-weight:400;font-size:18px;letter-spacing:1px;margin-bottom:14px}
.col li{list-style:none;font-size:13.5px;line-height:30px;padding-left:27px;position:relative}
.col li:before{content:"»";position:absolute;left:0;color:var(--gold)}
.col.c{width:300px}
.col.c li{padding-left:35px}
.col.c li:before{content:"";left:6px;top:11px;width:9px;height:9px;border-radius:50%;background:var(--gold)}
.chat{left:912px;top:232px;width:155px;height:54px;border-radius:27px;background:linear-gradient(180deg,var(--gold-light),var(--gold-dark));display:flex;align-items:center;gap:20px;padding-left:8px;font-weight:700;font-size:14px}
.chat i{width:40px;height:40px;border-radius:50%;background:var(--gold-dark)}
.copy{left:0;width:1200px;top:309px;border-top:1px solid #333a66;padding-top:22px;text-align:center;font-size:12px}
.copy em{font-style:normal;font-family:"Cinzel",serif;color:var(--gold-light)}
</style>
</head>
<body>

<header class="topbar">
  <div class="abs mail">EMAIL : INFO@VELLMOREFAMILYLAW.EXAMPLE</div>
  <div class="abs call">CALL US TOLL FREE - 24 HOURS A DAY</div>
  <div class="abs tel">( 555 ) 014 2290</div>
</header>

<header class="nav">
  <div class="abs brand">
    <div class="mark"></div>
    <div class="name">VELLMORE<small>FAMILY LAW</small><small>A LEGAL TECHNICIAN</small></div>
  </div>
  <nav class="abs menu">
    <span>HOME</span><span>ABOUT US</span><span>COLLABORATIVE LAW</span><span>COST AND FEES</span><span>MEDIATION</span><span>TRUSTING IN THE COLLABORATIVE PROCESS</span>
  </nav>
</header>

<section class="hero" role="img" aria-label="City skyline at sunset over the waterfront">
  <h1>Vellmore Family Law</h1>
  <p>Lorem ipsum dolor sit amet, consectetur adipiscing elit, sed do eiusmod tempor incididunt ut labore et dolore magna aliqua Ut enim ad minim veniam, quis nostrud exercitation ullamco.</p>
  <div class="btn" style="left:515px;top:324px;width:190px;height:46px">GET STARTED</div>
</section>

<section class="about">
  <div class="abs emblem"><span>VELLMORE<br>FAMILY LAW</span></div>
  <div class="abs label">ABOUT</div>
  <h2 class="h2">Vellmore Family Law</h2>
  <div class="rule"></div>
  <p>Sed ut perspiciatis unde omnis iste natus error sit voluptatem accusantium doloremque laudantium, totam rem aperiam, eaque ipsa quae ab illo inventore veritatis et quasi architecto beatae vitae dicta sunt explicabo. Nemo enim ipsam voluptatem quia voluptas sit aspernatur aut odit aut fugit, sed quia consequuntur magni dolores eos qui ratione voluptatem sequi nesciunt. Neque porro quisquam est, qui dolorem ipsum quia dolor sit amet.</p>
  <div class="btn" style="left:600px;top:330px;width:172px;height:48px">LEARN MORE</div>
</section>

<section class="services">
  <div class="abs eyebrow label">I SPECIALIZE IN</div>
  <h2 class="h2">Our Services</h2>
  <div class="rule"></div>
  <div class="abs vline"></div>
  <p class="abs intro">Lorem ipsum dolor sit amet, consectetur adipiscing elit, sed do eiusmod tempor incididunt ut labore et dolore magna aliqua. Quis ipsum suspendisse ultrices gravida. Risus commodo viverra maecenas accumsan lacus vel facilisis.</p>

  <div class="svc" style="left:78px">
    <svg class="icon" viewBox="0 0 84 84" role="img" aria-label="Handshake icon"><rect x="6" y="14" width="72" height="60" rx="8" fill="none" stroke="var(--gold)" stroke-width="3"/></svg>
    <h3>Collaborative Law</h3>
    <p>if uncontested divorce and parties are willing to work together.</p>
    <span class="learn">LEARN MORE</span>
  </div>
  <div class="svc-div" style="left:408px"></div>
  <div class="svc" style="left:446px">
    <svg class="icon" viewBox="0 0 84 84" role="img" aria-label="Document icon"><rect x="14" y="6" width="52" height="72" rx="4" fill="none" stroke="var(--gold)" stroke-width="3"/><path d="M24 26h32M24 38h32M24 50h20" stroke="var(--gold)" stroke-width="3"/></svg>
    <h3>Unbundled Services</h3>
    <p>if you need a limited amount of services and you prefer to do file for a divorce yourself to save money</p>
    <span class="learn">LEARN MORE</span>
  </div>
  <div class="svc-div" style="left:773px"></div>
  <div class="svc" style="left:818px">
    <svg class="icon" viewBox="0 0 84 84" role="img" aria-label="Meeting icon"><rect x="8" y="8" width="40" height="26" rx="4" fill="none" stroke="var(--gold)" stroke-width="3"/><rect x="36" y="20" width="40" height="26" rx="4" fill="none" stroke="var(--gold)" stroke-width="3"/><path d="M8 76h68" stroke="var(--gold)" stroke-width="3"/></svg>
    <h3>Mediation</h3>
    <p>if there are some issues that need to be resolved before filing for divorce</p>
    <span class="learn">LEARN MORE</span>
  </div>
</section>

<section class="video" role="img" aria-label="Hands holding paper family figures, video preview">
  <div class="abs play"><i><svg width="26" height="28" viewBox="0 0 26 28"><path d="M2 2l22 12L2 26z" fill="#fff"/></svg></i></div>
</section>

<section class="team">
  <div class="center eyebrow" style="top:83px">OUR ATTORNEYS</div>
  <div class="center h2" style="top:112px">Meet Our Team</div>
  <div class="arrow" style="left:87px;top:269px"><svg width="10" height="14"><path d="M8 1L2 7l6 6" fill="none" stroke="var(--gold)" stroke-width="2"/></svg></div>
  <div class="card" style="left:107px"><div class="photo" role="img" aria-label="Attorney portrait"></div><h4>JOHN DOE</h4><span class="learn">LEARN MORE</span></div>
  <div class="card" style="left:357px"><div class="photo" role="img" aria-label="Attorney portrait"></div><h4>JOHN DOE</h4><span class="learn">LEARN MORE</span></div>
  <div class="card" style="left:607px"><div class="photo" role="img" aria-label="Attorney portrait"></div><h4>JOHN DOE</h4><span class="learn">LEARN MORE</span></div>
  <div class="card" style="left:857px"><div class="photo" role="img" aria-label="Attorney portrait"></div><h4>JOHN DOE</h4><span class="learn">LEARN MORE</span></div>
  <div class="arrow" style="left:1073px;top:269px"><svg width="10" height="14"><path d="M2 1l6 6-6 6" fill="none" stroke="var(--gold)" stroke-width="2"/></svg></div>
</section>

<section class="testi">
  <div class="abs eyebrow label">CLIENT TESTIMONIALS</div>
  <h2 class="h2">You Can Trust Vellmore Family Law</h2>
  <div class="rule"></div>
  <div class="abs qm">“</div>
  <blockquote>Sed ut perspiciatis unde omnis iste natus error sit voluptatem accusantium doloremque laudantium, totam rem aperiam, eaque ipsa quae ab illo inventore veritatis et quasi architecto beatae vitae dicta sunt explicabo. Nemo enim ipsam voluptatem quia voluptas sit aspernatur aut odit aut fugit, sed quia consequuntur magni dolores eos qui ratione.</blockquote>
  <div class="abs avatar" role="img" aria-label="Client portrait"></div>
  <div class="abs who">Clara Whitfield</div>
  <div class="abs role">Lorem ipsum dolor</div>
  <i class="dot" style="top:237px"></i><i class="dot on" style="top:274px"></i><i class="dot" style="top:312px"></i><i class="dot" style="top:350px"></i>
</section>

<section class="blogs">
  <div class="center eyebrow" style="top:80px">LATEST BLOGS</div>
  <div class="center h2" style="top:110px">Our Latest Blogs &amp; Articles</div>
  <div class="arrow" style="left:32px;top:402px"><svg width="10" height="14"><path d="M8 1L2 7l6 6" fill="none" stroke="#333" stroke-width="2"/></svg></div>
  <article class="post" style="left:110px"><div class="thumb" role="img" aria-label="Couple signing documents" style="background:linear-gradient(135deg,#e8e2d6,#b7a58c)"></div><h4>Consectetur adipiscing elit, sed do eiusmod</h4><p>Lorem ipsum dolor sit amet, consectetur adipiscing elit, sed do eiusmod tempor incididunt ut labore et dolore</p><div class="meta"><span>by John doe</span><b>More information</b></div></article>
  <article class="post" style="left:443px"><div class="thumb" role="img" aria-label="Smiling family outdoors" style="background:linear-gradient(135deg,#8a7a52,#c9a77a)"></div><h4>Consectetur adipiscing elit, sed do eiusmod</h4><p>Lorem ipsum dolor sit amet, consectetur adipiscing elit, sed do eiusmod tempor incididunt ut labore et dolore</p><div class="meta"><span>by John doe</span><b>More information</b></div></article>
  <article class="post" style="left:777px"><div class="thumb" role="img" aria-label="Family meeting at a table" style="background:linear-gradient(135deg,#6e7690,#c0b2a0)"></div><h4>Consectetur adipiscing elit, sed do eiusmod</h4><p>Lorem ipsum dolor sit amet, consectetur adipiscing elit, sed do eiusmod tempor incididunt ut labore et dolore</p><div class="meta"><span>by John doe</span><b>More information</b></div></article>
  <div class="arrow" style="left:1122px;top:402px"><svg width="10" height="14"><path d="M2 1l6 6-6 6" fill="none" stroke="#333" stroke-width="2"/></svg></div>
</section>

<section class="contact">
  <div class="center h2" style="top:78px">We Are Here For You 24/7</div>
  <div class="rule" style="left:550px;top:136px;height:3px;background:#fff"></div>
  <div class="info" style="left:198px">
    <svg width="24" height="32" viewBox="0 0 24 32"><path d="M12 1C6 1 1 6 1 12c0 8 11 19 11 19s11-11 11-19C23 6 18 1 12 1z" fill="var(--gold)"/><circle cx="12" cy="12" r="4" fill="var(--navy)"/></svg>
    <div><b>Address</b><span>123 Lorem ipsum dolor sit<br>tetur adipiscing elit, sed d</span></div>
  </div>
  <div class="info" style="left:503px">
    <svg width="30" height="30" viewBox="0 0 30 30"><path d="M6 2l6 6-3 4c2 4 5 7 9 9l4-3 6 6-4 4C12 28 2 18 2 6z" fill="var(--gold)"/></svg>
    <div><b>Phone</b><span>555 014 2290</span></div>
  </div>
  <div class="info" style="left:745px">
    <svg width="40" height="28" viewBox="0 0 40 28"><rect x="1" y="1" width="38" height="26" fill="var(--gold)"/><path d="M1 1l19 14L39 1" fill="none" stroke="var(--navy)" stroke-width="2"/></svg>
    <div><b>Email</b><span>info@vellmorefamilylaw.example</span></div>
  </div>

  <div class="abs form">
    <svg class="abs" style="left:92px;top:70px" width="86" height="70" viewBox="0 0 86 70"><rect x="2" y="2" width="82" height="66" fill="var(--navy)"/><path d="M2 2l41 34L84 2M2 68l30-28M84 68L54 40" fill="none" stroke="#fff" stroke-width="3"/></svg>
    <div class="abs title">QUICK<br>INQUIRY</div>
    <div class="field" style="left:292px;top:80px">First Name *</div>
    <div class="field" style="left:625px;top:80px">Last Name *</div>
    <div class="field" style="left:292px;top:150px">Your Phone *</div>
    <div class="field" style="left:625px;top:150px">Your Email *</div>
    <div class="field" style="left:292px;top:220px;width:601px;height:82px">Message *</div>
    <div class="btn submit">COMPLETE A LONGER FORM THAT PREQUALIFIES THE VIEWER</div>
  </div>
</section>

<footer class="foot">
  <div class="abs logo"><i></i><span>VELLMORE<small>FAMILY LAW</small><small>A LEGAL TECHNICIAN</small></span></div>
  <p class="abs about-txt">Lorem ipsum dolor sit amet, consec tetur adipiscing elit, sed do eiusmod tempor incididunt ut labore et aliqua.</p>
  <div class="abs social"><i></i><i></i><i></i><i></i></div>
  <div class="col" style="left:425px"><h5>QUICK LINKS</h5><ul><li>Home</li><li>Collaborative Law</li><li>Cost and fees</li><li>Mediation</li></ul></div>
  <div class="col" style="left:615px"><h5>IMPORTANT</h5><ul><li>Privacy Policy</li><li>Refund Policy</li><li>Terms &amp; Conditions</li><li>About Us</li><li>Contact Us</li></ul></div>
  <div class="col c" style="left:828px"><h5>CONTACT INFO</h5><ul><li>123 Lorem ipsum dolor sit amet, consectetur adipiscing</li><li>+ 555 014 2290</li><li>info@vellmorefamilylaw.example</li></ul></div>
  <div class="abs chat"><i></i>CHAT</div>
  <div class="abs copy">© Copyrights 2021 &nbsp;<em>Vellmore Family Law</em>&nbsp; | &nbsp; All Rights Reserved</div>
</footer>

</body>
</html>
```